Crimson Ridge Footrace Co.

We need a website (wordpress) design for a new website that we will be launching. This is for a new trail racing series in Canada.
We recently had a logo designed so want to incorporate the colours of the logo on the website design. Especially the dark blue, green and orange.
Websites that we like for comparison of trail running race themes are:
https://www.mosslinerunning.com/
https://www.bramblestridecup.com/
http://www.quarrypathcircuit.ca/
https://www.cobaltcreekchase.com/
http://www.dunmoorrunningtour.com/

Target Market(s)

Outdoor trail runners

Coding

Coded - Design and coding required

Number of Pages Required

4 page

Font styles to use
Sans Serif

Colors
0255a3
33b8a4
f37122

Requirements
Must have
• There will be a main page with eye catching design noting what we do. Page 2 and 3 will be for each race in the series. Page 1 will be a specific race, and page 2 with be for another race. page 3 and 4 will be for future races that we add so that each race has their own page.
• Our races all take place in the mountains, so using graphics including mountains, rivers, trees is all a requirement for us.
• Our logo is attached, we want to use the colours of the logo in the website design.
Nice to have
• Outdoor theme is a nice to have. We like wood and earth tone colours, and pictures/graphics of runners and mountains and trees.
• There are 4 people involved in our organization. We'd like a photo and brief blurb of each of us, similar to how this website did their layout: https://www.mosslinerunning.com/

```html
<!DOCTYPE html>
<html lang="en">
<head>
<meta charset="utf-8">
<title>Crimson Ridge Footrace Co. — Trail Racing</title>
<link rel="stylesheet" href="https://fonts.googleapis.com/css2?family=Roboto+Condensed:wght@400;700&family=Open+Sans:ital,wght@0,400;0,600;1,400&display=swap">
<style>
:root{
  --blue:#0255a3;
  --teal:#33b8a4;
  --orange:#f37122;
  --navy:#141d2b;
  --navy-soft:#1f2b3d;
  --forest:#17291e;
  --gold:#b8943a;
  --ink:#222;
  --muted:#555;
  --wood-light:#f4f2ec;
  --wood-mid:#e2ded4;
  --wood-warm:#ece8df;
  --white:#fff;
}
*{box-sizing:border-box;margin:0;padding:0}
html,body{width:1200px;height:3913px;overflow:hidden}
body{position:relative;background:var(--wood-light);font-family:"Open Sans",Arial,sans-serif;color:var(--ink)}
.heading{font-family:"Roboto Condensed","Arial Narrow",sans-serif;font-weight:400}
section,header,footer{position:absolute;left:0;width:1200px}

/* Whitewashed wood backdrop */
.wood{position:absolute;inset:0;background:
  linear-gradient(100deg,var(--wood-light) 0%,var(--wood-mid) 22%,var(--wood-warm) 48%,var(--wood-mid) 74%,var(--wood-light) 100%)}

/* Hero */
.hero{top:0;height:680px;overflow:hidden}
.hero-photo{position:absolute;inset:0;background:linear-gradient(160deg,#9fb4c6 0%,#dfe5ea 28%,#6f7f62 55%,#4d5a37 75%,#7a6a4c 100%)}
.hero-edge{position:absolute;left:0;bottom:0;width:1200px;height:140px}
.brand{position:absolute;left:78px;top:40px;display:flex;align-items:center;gap:10px;color:var(--white);font-family:"Roboto Condensed",sans-serif;font-weight:700;font-size:20px;line-height:1.05;width:160px}
.brand-dot{width:22px;height:22px;border-radius:50%;background:var(--orange);flex:none}
.topbar{position:absolute;right:80px;top:44px;display:flex;align-items:center;gap:26px;color:var(--white);font-family:"Roboto Condensed",sans-serif;font-size:21px}
.burger{width:24px;height:18px;display:flex;flex-direction:column;justify-content:space-between}
.burger span{height:3px;background:var(--white)}
.phone{display:flex;align-items:center;gap:8px}
.hero-title{position:absolute;top:226px;width:1200px;text-align:center;color:var(--white);font-family:"Roboto Condensed",sans-serif;font-weight:700;font-size:84px;line-height:1;text-shadow:0 2px 8px rgba(0,0,0,.35)}
.hero-sub{position:absolute;top:318px;width:1200px;text-align:center;color:var(--white);font-family:"Roboto Condensed",sans-serif;font-size:36px;line-height:1;text-shadow:0 2px 6px rgba(0,0,0,.35)}
.dots{position:absolute;right:46px;top:312px;display:flex;flex-direction:column;gap:11px}
.dots span{width:8px;height:8px;border-radius:50%;background:var(--white)}

/* Welcome */
.welcome{top:680px;height:670px}
.welcome h2{position:absolute;top:0;width:1200px;text-align:center;font-size:36px;color:#1b1b1b}
.welcome h2 em{font-style:normal;color:var(--orange)}
.welcome .lead{position:absolute;top:70px;left:170px;width:860px;text-align:center;font-size:14.5px;line-height:1.95;color:var(--muted)}
.feature{position:absolute;top:272px;width:295px;height:243px;background:var(--white);border:1px solid #d8d8d8;box-shadow:0 3px 8px rgba(0,0,0,.08);text-align:center}
.feature .icon{position:absolute;left:89px;top:-62px;width:116px;height:116px;border-radius:50%;display:flex;align-items:center;justify-content:center}
.feature h3{margin-top:80px;font-size:21px;color:#222}
.feature p{margin:14px 30px 0;font-size:13.5px;line-height:1.9;color:var(--muted)}
.btn{position:absolute;left:95px;bottom:-18px;width:105px;height:36px;border-radius:18px;border:1px solid #999;background:var(--white);font-size:12.5px;line-height:34px;color:#333}
.btn.is-active{background:var(--orange);border-color:var(--orange);color:var(--white)}

/* Races */
.races{top:1349px;height:648px;background:linear-gradient(180deg,var(--navy-soft),var(--navy) 60%,#1a2232)}
.races h2{position:absolute;top:72px;width:1200px;text-align:center;color:var(--white);font-size:40px}
.race{position:absolute;top:172px;width:316px;height:381px;background:var(--white)}
.race .photo{height:193px}
.race h3{margin-top:30px;text-align:center;font-size:19px;color:#222}
.race p{margin:16px 28px 0;text-align:center;font-size:13.5px;line-height:1.75;color:var(--muted)}
.race .more{display:block;margin-top:12px;text-align:center;font-size:13px;color:var(--orange)}

/* Team */
.team{top:1997px;height:964px}
.team h2{position:absolute;top:122px;width:1200px;text-align:center;font-size:42px;color:#1a1a1a}
.member{position:absolute;width:501px;height:264px;display:flex}
.member .bio{width:292px;background:var(--navy);color:var(--white);font-size:13.5px;line-height:1.75;padding:34px 26px 0;text-align:center}
.member .bio p+p{margin-top:18px}
.member .portrait{position:relative;flex:1}
.member .portrait span{position:absolute;left:0;right:0;bottom:16px;text-align:center;color:var(--white);font-size:13px}

/* Testimonial */
.testimonial{top:2961px;height:700px;background:linear-gradient(180deg,#d9ddd8 0%,#c4ccc0 40%,#9fae97 75%,#7f8d72 100%)}
.testimonial h2{position:absolute;top:60px;width:1200px;text-align:center;font-size:40px;color:#1d1d1d}
.quote-card{position:absolute;left:125px;top:162px;width:945px;height:287px;background:var(--white);border:2px solid #cfcfcf;box-shadow:0 4px 12px rgba(0,0,0,.15)}
.quote-card .avatar{position:absolute;left:37px;top:53px;width:166px;height:166px;border-radius:50%}
.quote-card blockquote{position:absolute;left:292px;top:60px;width:610px;font-size:18.5px;line-height:31px;color:#333;text-align:justify}
.mark{position:absolute;font-family:Georgia,serif;font-weight:700;font-size:52px;color:#111;line-height:1}
.mark-end{position:relative;top:14px;margin-left:10px;font-family:Georgia,serif;font-weight:700;font-size:52px;line-height:0;color:#111}
.quote-card cite{position:absolute;left:297px;top:206px;font-size:15.5px;color:#444}
.arrows{position:absolute;left:982px;top:471px;display:flex;gap:18px}

/* Footer */
.site-footer{top:3590px;height:323px}
.footer-band{position:absolute;inset:0}
.footer-brand{position:absolute;top:80px;width:1200px;color:var(--white);font-family:"Roboto Condensed",sans-serif;font-weight:700;font-size:24px;display:flex;justify-content:center;align-items:center;gap:10px}
.footer-nav{position:absolute;top:160px;width:1200px;display:flex;justify-content:center;gap:40px;font-size:16px;color:var(--white)}
.social{position:absolute;top:207px;width:1200px;display:flex;justify-content:center;gap:11px}
.social span{width:33px;height:33px;border-radius:50%;border:2px solid var(--white)}
.copyright{position:absolute;top:262px;width:1200px;text-align:center;font-size:13px;color:#d8d8d8}
</style>
</head>
<body>

<header class="hero">
  <div class="hero-photo" role="img" aria-label="Trail runners climbing a rocky alpine path below snowy peaks"></div>
  <div class="brand"><span class="brand-dot"></span>Crimson Ridge Footrace Co.</div>
  <div class="topbar">
    <div class="burger"><span></span><span></span><span></span></div>
    <div class="phone">
      <svg width="17" height="17" viewBox="0 0 24 24"><path fill="#fff" d="M6.6 10.8a15.1 15.1 0 0 0 6.6 6.6l2.2-2.2c.3-.3.7-.4 1-.2 1.1.4 2.3.6 3.6.6.6 0 1 .4 1 1V20c0 .6-.4 1-1 1C10.6 21 3 13.4 3 4c0-.6.4-1 1-1h3.5c.6 0 1 .4 1 1 0 1.3.2 2.5.6 3.6.1.3 0 .7-.2 1z"/></svg>
      1.800.555.0147
    </div>
  </div>
  <h1 class="hero-title">TRAIL RACING</h1>
  <p class="hero-sub">Neque porro quisquam dolorem</p>
  <div class="dots"><span></span><span></span><span></span></div>
  <svg class="hero-edge" viewBox="0 0 1200 140" preserveAspectRatio="none">
    <polygon fill="#f2f0ea" points="0,20 60,55 120,35 190,80 260,60 330,95 400,70 470,100 540,60 610,85 680,40 750,75 820,55 890,90 960,65 1030,95 1100,70 1160,85 1200,60 1200,140 0,140"/>
  </svg>
</header>

<section class="welcome">
  <div class="wood" role="img" aria-label="Whitewashed weathered wood plank background"></div>
  <h2 class="heading">Welcome to <em>Crimson Ridge Footrace Co.</em></h2>
  <p class="lead">It is a long established fact that a reader will be distracted by the readable content of a page when looking at its layout. The point of using Lorem Ipsum is that it has a more-or-less normal distribution of letters, as opposed to using 'Content here, content here', making it look like readable English. Many desktop publishing packages and web page editors</p>

  <article class="feature" style="left:130px">
    <div class="icon" style="background:var(--blue)">
      <svg width="56" height="44" viewBox="0 0 56 44"><g stroke="#fff" stroke-width="5" stroke-linecap="round" fill="none"><path d="M4 12h20M10 22h18M4 32h20"/><path d="M32 8l16 14-16 14"/></g></svg>
    </div>
    <h3 class="heading">Run</h3>
    <p>It is a long established fact that a reader will be distracted by the readable content of a page</p>
    <span class="btn">Read more</span>
  </article>

  <article class="feature" style="left:457px">
    <div class="icon" style="background:var(--orange)">
      <svg width="48" height="52" viewBox="0 0 48 52"><path d="M10 4v46" stroke="#fff" stroke-width="5" stroke-linecap="round"/><path fill="#fff" d="M12 6h28l-7 9 7 9H12z"/></svg>
    </div>
    <h3 class="heading">Trail Racing</h3>
    <p>It is a long established fact that a reader will be distracted by the readable content of a page</p>
    <span class="btn is-active">Read more</span>
  </article>

  <article class="feature" style="left:783px">
    <div class="icon" style="background:var(--teal)">
      <svg width="64" height="40" viewBox="0 0 64 40"><path fill="#fff" d="M0 40 22 6l12 18 8-10 22 26z"/></svg>
    </div>
    <h3 class="heading">Adventure</h3>
    <p>It is a long established fact that a reader will be distracted by the readable content of a page</p>
    <span class="btn">Read more</span>
  </article>
</section>

<section class="races">
  <h2 class="heading">Trail Racing</h2>
  <article class="race" style="left:99px">
    <div class="photo" role="img" aria-label="Group of runners on a forest trail" style="background:linear-gradient(160deg,#3f5a3a,#24331f 60%,#5c5a48)"></div>
    <h3 class="heading">Neque porro quisquam dolorem</h3>
    <p>The point of using Lorem Ipsum is that it has a more-or-less normal distribution of letters, as opposed to using</p>
    <span class="more">Read More »</span>
  </article>
  <article class="race" style="left:441px">
    <div class="photo" role="img" aria-label="Runners on a dirt path through autumn woods" style="background:linear-gradient(160deg,#6a5a3a,#8a6d44 50%,#4a4630)"></div>
    <h3 class="heading">Dolorem ipsum dolor sit amet</h3>
    <p>The point of using Lorem Ipsum is that it has a more-or-less normal distribution of letters, as opposed to using</p>
    <span class="more">Read More »</span>
  </article>
  <article class="race" style="left:785px">
    <div class="photo" role="img" aria-label="Runner on a rocky hillside trail under blue sky" style="background:linear-gradient(180deg,#8fb2d6,#b6c8d8 40%,#6c6a4a 70%,#8a5f44)"></div>
    <h3 class="heading">Porro quisquam dolorem</h3>
    <p>The point of using Lorem Ipsum is that it has a more-or-less normal distribution of letters, as opposed to using</p>
    <span class="more">Read More »</span>
  </article>
</section>

<section class="team">
  <div class="wood" role="img" aria-label="Whitewashed weathered wood plank background"></div>
  <h2 class="heading">Our Team</h2>

  <div class="member" style="left:89px;top:236px">
    <div class="bio"><p>The point of using Lorem Ipsum is that it has a more-or-less normal distribution of letters, as opposed to using 'Content here, content here',</p><p>Making it look like readable English Many desktop publishing packages and web page editors now use Lorem Ipsum as their default model text,</p></div>
    <div class="portrait" role="img" aria-label="Portrait of a team member" style="background:linear-gradient(160deg,#c9c9c9,#8e8e8e)"><span>Ratione ipsum</span></div>
  </div>

  <div class="member" style="left:613px;top:236px">
    <div class="portrait" role="img" aria-label="Portrait of a team member" style="background:linear-gradient(160deg,#b9b9bd,#5a6478)"><span>Consecte ipsum</span></div>
    <div class="bio"><p>It is a long established fact that a reader will be distracted by the readable content of a page when looking at its layout,</p><p>Making it look like readable English Many desktop publishing packages and web page editors now use Lorem Ipsum as their default model text,</p></div>
  </div>

  <div class="member" style="left:89px;top:521px">
    <div class="bio"><p>The point of using Lorem Ipsum is that it has a more-or-less normal distribution of letters, as opposed to using 'Content here, content here',</p><p>Making it look like readable English Many desktop publishing packages and web page editors now use Lorem Ipsum as their default model text,</p></div>
    <div class="portrait" role="img" aria-label="Portrait of a team member" style="background:linear-gradient(160deg,#d0d0d0,#6e7a6a)"><span>Nequeporro</span></div>
  </div>

  <div class="member" style="left:613px;top:521px">
    <div class="portrait" role="img" aria-label="Portrait of a team member outdoors" style="background:linear-gradient(160deg,#a48a6a,#4a3a2c)"><span>Ipsum quia</span></div>
    <div class="bio"><p>Lorem Ipsum has been the industry's standard dummy text ever since the 1500s, when an unknown printer took a galley of type and scrambled</p><p>Making it look like readable English Many desktop publishing packages and web page editors now use Lorem Ipsum as their default model text,</p></div>
  </div>
</section>

<section class="testimonial" role="img" aria-label="Hazy mountain valley with a trail">
  <h2 class="heading">Testimonial</h2>
  <div class="quote-card">
    <div class="avatar" role="img" aria-label="Portrait of the reviewer" style="background:linear-gradient(160deg,#4d6a7a,#1f3340)"></div>
    <span class="mark" style="left:255px;top:52px">“</span>
    <blockquote>The point of using Lorem Ipsum is that it has a more-or-less normal distribution of letters, as opposed to using 'Content here, content here', making it look like readable English. Many desktop publishing packages and web page editors now use Lorem Ipsum<span class="mark-end">”</span></blockquote>
    <cite>Helena Marsh, CFO, Alder Peak Holdings</cite>
  </div>
  <div class="arrows">
    <svg width="32" height="18" viewBox="0 0 32 18"><path d="M30 9H4M11 2 3 9l8 7" stroke="#e08a1e" stroke-width="3.5" fill="none" stroke-linecap="round"/></svg>
    <svg width="32" height="18" viewBox="0 0 32 18"><path d="M2 9h26M21 2l8 7-8 7" stroke="#111" stroke-width="3.5" fill="none" stroke-linecap="round"/></svg>
  </div>
</section>

<footer class="site-footer">
  <svg class="footer-band" viewBox="0 0 1200 323" preserveAspectRatio="none">
    <polygon fill="#17291e" points="0,50 80,20 150,55 230,30 300,70 370,40 440,75 520,45 600,20 680,50 760,30 840,65 920,35 1000,60 1080,25 1150,50 1200,35 1200,323 0,323"/>
    <polyline fill="none" stroke="#b8943a" stroke-width="5" points="0,50 80,20 150,55 230,30 300,70 370,40 440,75 520,45 600,20 680,50 760,30 840,65 920,35 1000,60 1080,25 1150,50 1200,35"/>
  </svg>
  <div class="footer-brand"><span class="brand-dot"></span>Crimson Ridge Footrace Co.</div>
  <nav class="footer-nav"><span>Home</span><span>About us</span><span>Service</span><span>Blog</span><span>Contact us</span></nav>
  <div class="social"><span></span><span></span><span></span><span></span><span></span></div>
  <p class="copyright">Copyright © 2018 All Rights Reserved</p>
</footer>

</body>
</html>
```